Meridale Bed Company Needs Business Card

Looking for a very nice looking business card. Creative but not extravagant. We sell beds and pillows across the U.S. and need something professional but catchy. I have attached the logo.

Name : Devin Holt
Title : President
Phone : (800) 471-2960
Email: sleep@quilmora.com
Website: www.quilmora.com

Can be single-sided or double-sided
horizontal or vertical

Can use Blues/Greys

Target Market(s)

Mass Market

Industry/Entity Type

Retail

Contact Information for Business Card

Name : Devin Holt
Title : President
Phone : (800) 471-2960
Email: sleep@quilmora.com
Website: www.quilmora.com

Requirements
Must have
• Clean, Modern, Smooth
• Can use Blues/Greys
• On the other side without the information - have something simple like www.quilmora.com or our logo
Nice to have
• Surprise me
Should not have
• Nothing crazy, nothing cluttered

```html
<!DOCTYPE html>
<html lang="en">
<head>
<meta charset="utf-8">
<title>Meridale Bed Company — Business Card</title>
<link href="https://fonts.googleapis.com/css2?family=Raleway:wght@400;600&display=swap" rel="stylesheet">
<style>
  :root {
    --backdrop: #e9ecef;
    --card-dark: #262626;
    --card-light: #ffffff;
    --brand-blue: #29a3db;
    --ink: #2b2b2b;
    --ink-soft: #444444;
    --ghost: #f1f1f1;
    --bar-dark: #1e1e1e;
  }
  * { box-sizing: border-box; margin: 0; padding: 0; }
  html, body {
    width: 1200px;
    height: 863px;
    overflow: hidden;
  }
  body {
    background: var(--backdrop);
    font-family: "Raleway", sans-serif;
    display: flex;
    align-items: center;
    justify-content: center;
    gap: 80px;
  }
  .card {
    position: relative;
    width: 300px;
    height: 525px;
    overflow: hidden;
    box-shadow: 0 6px 18px rgba(0, 0, 0, 0.12);
  }

  /* Back side */
  .card--back { background: var(--card-dark); }
  .back-brand {
    position: absolute;
    left: 30px;
    bottom: 46px;
    display: flex;
    align-items: center;
    gap: 10px;
  }
  .back-brand__mark {
    width: 10px;
    height: 10px;
    background: var(--brand-blue);
  }
  .back-brand__name {
    color: var(--brand-blue);
    font-weight: 400;
    font-size: 26px;
    line-height: 1;
  }

  /* Front side */
  .card--front { background: var(--card-light); }
  .front-watermark {
    position: absolute;
    right: 14px;
    bottom: 44px;
    writing-mode: vertical-rl;
    transform: rotate(180deg);
    color: var(--ghost);
    font-weight: 400;
    font-size: 80px;
    line-height: 1;
  }
  .identity {
    position: absolute;
    left: 0;
    top: 178px;
  }
  .identity__marker {
    position: absolute;
    left: 0;
    top: 9px;
    width: 20px;
    height: 9px;
    background: var(--bar-dark);
  }
  .identity__name {
    margin-left: 28px;
    color: var(--brand-blue);
    font-weight: 600;
    font-size: 23px;
    line-height: 1.15;
  }
  .identity__title {
    margin-left: 20px;
    color: var(--ink);
    font-weight: 400;
    font-size: 16px;
    line-height: 1.2;
  }
  .contact-list {
    position: absolute;
    left: 22px;
    bottom: 40px;
    list-style: none;
  }
  .contact-list__item {
    display: flex;
    align-items: center;
    gap: 10px;
    height: 26px;
    color: var(--ink-soft);
    font-size: 14px;
    font-weight: 400;
  }
  .contact-list__icon {
    width: 17px;
    height: 17px;
    flex: none;
  }
</style>
</head>
<body>

  <section class="card card--back" aria-label="Business card, back side">
    <div class="back-brand">
      <span class="back-brand__mark"></span>
      <span class="back-brand__name">Quilmora</span>
    </div>
  </section>

  <section class="card card--front" aria-label="Business card, front side">
    <div class="front-watermark" aria-hidden="true">Quilmora</div>

    <div class="identity">
      <span class="identity__marker"></span>
      <p class="identity__name">Devin Holt</p>
      <p class="identity__title">President</p>
    </div>

    <ul class="contact-list">
      <li class="contact-list__item">
        <svg class="contact-list__icon" viewBox="0 0 20 20" aria-hidden="true">
          <circle cx="10" cy="10" r="10" fill="var(--brand-blue)"/>
          <path d="M5 8.5 Q10 4.5 15 8.5 L13.6 10 L11.8 9 L11.8 8 Q10 7.4 8.2 8 L8.2 9 L6.4 10 Z" fill="#fff"/>
          <rect x="6.6" y="10.4" width="6.8" height="4.2" rx="0.8" fill="#fff"/>
        </svg>
        <span>(800) 471-2960</span>
      </li>
      <li class="contact-list__item">
        <svg class="contact-list__icon" viewBox="0 0 20 20" aria-hidden="true">
          <circle cx="10" cy="10" r="10" fill="var(--brand-blue)"/>
          <rect x="5" y="6.5" width="10" height="7" rx="0.8" fill="#fff"/>
          <path d="M5.4 7 L10 10.6 L14.6 7" fill="none" stroke="var(--brand-blue)" stroke-width="1"/>
        </svg>
        <span>sleep@quilmora.com</span>
      </li>
      <li class="contact-list__item">
        <svg class="contact-list__icon" viewBox="0 0 20 20" aria-hidden="true">
          <circle cx="10" cy="10" r="10" fill="var(--brand-blue)"/>
          <g fill="none" stroke="#fff" stroke-width="1.6" stroke-linecap="round">
            <rect x="4.6" y="8.6" width="6" height="3.6" rx="1.8" transform="rotate(-45 7.6 10.4)"/>
            <rect x="9.4" y="7.8" width="6" height="3.6" rx="1.8" transform="rotate(-45 12.4 9.6)"/>
          </g>
        </svg>
        <span>www.quilmora.com</span>
      </li>
    </ul>
  </section>

</body>
</html>
```